Whitcombe Business Card Design

The name of the business is Dario Whitcombe, CPA LLC
The service that we offer is Accounting, Tax & Consulting Services. I need it to have the following items:
Dario Whitcombe, Principal
Phone Number
Email Address
Physical Address

I have attached the company logo, one in black and one in white. Please provide a design in black background and the other in white background. Please include "Accounting, Tax & Consulting Services". I want the business card to be clean and very professional.

```html
<!DOCTYPE html>
<html lang="en">
<head>
<meta charset="utf-8">
<title>Dario Whitcombe, CPA LLC — Business Card</title>
<link rel="stylesheet" href="https://fonts.googleapis.com/css2?family=Montserrat:wght@400;500;600;700;800&family=Rubik:wght@700&display=swap">
<style>
  :root {
    --bg: #d9d9d9;
    --card-white: #ffffff;
    --brand-red: #8e050b;
    --brand-red-dark: #6f0307;
    --ink: #2b2b2b;
    --ink-soft: #555555;
    --faint: #ececec;
    --bar-dark: #2e2e31;
  }
  * { box-sizing: border-box; margin: 0; padding: 0; }
  html, body { width: 1200px; height: 800px; overflow: hidden; }
  body {
    background: var(--bg);
    font-family: "Montserrat", sans-serif;
    display: flex;
    align-items: center;
    justify-content: center;
    gap: 40px;
  }
  .card {
    position: relative;
    width: 540px;
    height: 309px;
    overflow: hidden;
    box-shadow: 0 10px 30px rgba(0,0,0,0.18);
  }

  /* Front */
  .card-front { background: var(--card-white); }
  .accent-bar-top {
    position: absolute; top: 0; right: 34px;
    width: 16px; height: 92px;
    background: var(--brand-red);
  }
  .accent-bar-bottom {
    position: absolute; bottom: 0; left: 34px;
    width: 16px; height: 92px;
    background: var(--bar-dark);
  }
  .company-block {
    position: absolute; left: 70px; top: 58px;
  }
  .company-mark {
    display: flex; align-items: center; gap: 8px;
  }
  .company-mark .mark-square {
    width: 14px; height: 14px; background: var(--brand-red);
  }
  .company-name {
    font-size: 17px; font-weight: 600; color: var(--ink);
    letter-spacing: 0.02em;
  }
  .company-title {
    margin-top: 6px;
    font-size: 10.5px; font-weight: 500; color: var(--ink-soft);
    letter-spacing: 0.16em; text-transform: uppercase;
  }
  .contact-list {
    position: absolute; left: 70px; top: 142px;
    list-style: none;
    font-size: 11.5px; color: var(--ink); line-height: 1.55;
  }
  .contact-list li { display: flex; align-items: flex-start; gap: 9px; }
  .contact-list svg { flex: none; width: 11px; height: 11px; margin-top: 3px; fill: var(--brand-red); }
  .contact-list .indent { padding-left: 20px; }

  .faint-square {
    position: absolute; right: 60px; top: 86px;
    width: 150px; height: 150px;
    border: 16px solid var(--faint);
  }
  .principal-block {
    position: absolute; right: 64px; top: 150px;
    text-align: right;
  }
  .principal-name {
    font-family: "Rubik", sans-serif;
    font-size: 20px; font-weight: 700; color: #1d1d1d;
    letter-spacing: 0.03em; text-transform: uppercase;
    background: rgba(255,255,255,0.85); padding: 0 4px;
  }
  .principal-role {
    font-size: 12px; font-weight: 500; color: var(--brand-red);
    letter-spacing: 0.04em; padding-right: 4px;
  }

  /* Back */
  .card-back {
    background: linear-gradient(135deg, var(--brand-red-dark) 0%, var(--brand-red) 45%, var(--brand-red) 100%);
    display: flex; flex-direction: column; align-items: center; justify-content: center;
  }
  .back-mark {
    display: flex; align-items: center; gap: 12px;
  }
  .back-mark .mark-square {
    width: 22px; height: 22px; background: #ffffff;
  }
  .back-name {
    font-size: 26px; font-weight: 700; color: #ffffff;
    letter-spacing: 0.04em;
  }
  .tagline {
    margin-top: 46px;
    font-family: "Rubik", sans-serif;
    font-size: 13px; font-weight: 700; color: #ffffff;
    letter-spacing: 0.05em; text-transform: uppercase;
  }
</style>
</head>
<body>
  <section class="card card-front" aria-label="Business card front">
    <div class="accent-bar-top"></div>
    <div class="accent-bar-bottom"></div>

    <div class="company-block">
      <div class="company-mark">
        <span class="mark-square"></span>
        <span class="company-name">Dario Whitcombe, CPA LLC</span>
      </div>
      <p class="company-title">Certified Public Accountant</p>
    </div>

    <ul class="contact-list">
      <li>
        <svg viewBox="0 0 12 12"><path d="M6 0a4 4 0 0 0-4 4c0 3 4 8 4 8s4-5 4-8a4 4 0 0 0-4-4zm0 5.5A1.5 1.5 0 1 1 6 2.5a1.5 1.5 0 0 1 0 3z"/></svg>
        <span>4120 Larkspur Court</span>
      </li>
      <li class="indent">Fairbanks, Alaska 99712</li>
      <li>
        <svg viewBox="0 0 12 12"><path d="M2.5 0.5l2 2.5-1.2 1.3c.7 1.6 2 2.9 3.6 3.6L8.2 6.7l2.5 2-1 2.4C5 11 1 7 0.8 2.3z"/></svg>
        <span>907-555-0148</span>
      </li>
      <li>
        <svg viewBox="0 0 12 12"><path d="M0 2h12v8H0z M0.8 2.6L6 6.6l5.2-4" fill="var(--brand-red)"/><path d="M0.8 2.8L6 6.6l5.2-3.8" fill="none" stroke="#fff" stroke-width="1"/></svg>
        <span>dario@whitcombecpa.com</span>
      </li>
      <li>
        <svg viewBox="0 0 12 12"><circle cx="6" cy="6" r="6"/><path d="M0 6h12M6 0c-2.5 3-2.5 9 0 12M6 0c2.5 3 2.5 9 0 12" fill="none" stroke="#fff" stroke-width="0.9"/></svg>
        <span>www.whitcombecpa.com</span>
      </li>
    </ul>

    <div class="faint-square"></div>
    <div class="principal-block">
      <p class="principal-name">Dario Whitcombe</p>
      <p class="principal-role">Principal</p>
    </div>
  </section>

  <section class="card card-back" aria-label="Business card back">
    <div class="back-mark">
      <span class="mark-square"></span>
      <span class="back-name">Dario Whitcombe</span>
    </div>
    <p class="tagline">Accounting, Tax &amp; Consulting Services</p>
  </section>
</body>
</html>
```